Business Card Design

Online clothing womens clothing store, I sell my clothing online and at the markets.

i would like the attached picture on the front of the card and the contact information on the back.

Industry/Entity Type

Business

Contact Information for Business Card

Marlow Thread
Karen Whitfield
(Instagram symbol) _marlow_thread_
(Facebook symbol) www.fakebookexample.com/marlowthreadau/

W : www.marlowthread.example.au
E : info@marlowthread.example.au
P : 0498716204

```html
<!DOCTYPE html>
<html lang="en">
<head>
<meta charset="utf-8">
<title>Marlow Thread – Business Card</title>
<link href="https://fonts.googleapis.com/css2?family=Source+Sans+3:wght@400;600;700&display=swap" rel="stylesheet">
<style>
  :root {
    --backdrop: #a3a3a3;
    --card-dark: #303135;
    --card-dark-edge: #34353a;
    --rule: #8a8b8f;
    --ink-light: #ffffff;
    --ink-soft: #e6e6e6;
    --photo-mist: #6b6e6c;
    --photo-teal: #4a5c5a;
    --photo-deep: #22292a;
  }
  * { margin: 0; padding: 0; box-sizing: border-box; }
  html, body {
    width: 1200px; height: 900px; overflow: hidden;
    background: var(--backdrop);
    font-family: "Source Sans 3", "Myriad Pro", Arial, sans-serif;
  }
  .stage { position: relative; width: 1200px; height: 900px; }

  .card {
    position: absolute; top: 271px;
    width: 457px; height: 281px;
    border-radius: 12px; overflow: hidden;
  }

  /* Contact side */
  .card-back {
    left: 137px;
    background: linear-gradient(180deg, var(--card-dark-edge), var(--card-dark));
    color: var(--ink-light);
  }
  .name-row {
    position: absolute; left: 0; right: 0; top: 115px;
    display: flex; align-items: center; gap: 5px;
  }
  .name-row::before, .name-row::after {
    content: ""; flex: 1; height: 1px; background: var(--rule); margin-top: 2px;
  }
  .holder-name {
    font-size: 19px; font-weight: 700; line-height: 24px; white-space: nowrap;
  }
  .social-list {
    position: absolute; left: 24px; top: 176px;
    list-style: none; font-size: 13px; line-height: 19px; color: var(--ink-soft);
  }
  .social-list li { display: flex; align-items: center; gap: 12px; }
  .social-mark {
    width: 9px; height: 9px; background: var(--ink-soft); border-radius: 1px;
  }
  .contact-list {
    position: absolute; right: 30px; top: 166px;
    list-style: none; font-size: 13.5px; line-height: 19.5px; color: var(--ink-soft);
    text-align: right;
  }
  .contact-list li { display: flex; justify-content: flex-end; align-items: center; gap: 8px; }
  .contact-list svg { width: 12px; height: 12px; flex: none; }

  /* Brand side */
  .card-front { left: 626px; }
  .photo-area {
    position: absolute; inset: 0;
    background:
      radial-gradient(ellipse 55% 75% at 80% 45%, var(--photo-deep) 0%, rgba(34,41,42,0.6) 45%, rgba(34,41,42,0) 75%),
      linear-gradient(90deg, var(--photo-mist) 0%, #636866 40%, var(--photo-teal) 70%, #394443 100%);
  }
  .brand-name {
    position: absolute; left: 58px; top: 204px; width: 352px;
    font-size: 44px; font-weight: 600; letter-spacing: 0.5px; line-height: 50px;
    color: var(--ink-light); text-transform: uppercase; white-space: nowrap;
    text-align: center;
  }
</style>
</head>
<body>
<main class="stage">
  <section class="card card-back" aria-label="Contact side">
    <div class="name-row"><h1 class="holder-name">Karen Whitfield</h1></div>

    <ul class="social-list">
      <li><span class="social-mark"></span>_marlow_thread_</li>
      <li><span class="social-mark"></span>/marlowthreadau/</li>
    </ul>

    <ul class="contact-list">
      <li>0498716204
        <svg viewBox="0 0 12 12" aria-hidden="true"><path d="M2.5 1 L4.5 1 L5.2 3.5 L4 4.5 Q5 7 7.5 8 L8.5 6.8 L11 7.5 L11 9.5 Q10.5 11 9 11 Q2 10 1 3 Q1 1.5 2.5 1Z" fill="#ffffff"/></svg>
      </li>
      <li>info@marlowthread.example.au
        <svg viewBox="0 0 12 12" aria-hidden="true"><rect x="1" y="2.5" width="10" height="7" fill="#ffffff"/><path d="M1 2.5 L6 6.5 L11 2.5" stroke="#303135" stroke-width="1" fill="none"/></svg>
      </li>
      <li>www.marlowthread.example.au
        <svg viewBox="0 0 12 12" aria-hidden="true"><g fill="none" stroke="#ffffff" stroke-width="1.3" stroke-linecap="round"><path d="M5 7 L7 5"/><path d="M4.2 5.6 L2.6 7.2 A1.7 1.7 0 0 0 4.8 9.4 L6.4 7.8"/><path d="M7.8 6.4 L9.4 4.8 A1.7 1.7 0 0 0 7.2 2.6 L5.6 4.2"/></g></svg>
      </li>
    </ul>
  </section>

  <section class="card card-front" aria-label="Brand side">
    <div class="photo-area" role="img" aria-label="Moody teal-grey fashion photograph of a woman with voluminous dark hair"></div>
    <p class="brand-name">Marlow Thread</p>
  </section>
</main>
</body>
</html>
```